Website for a Psychologist in Private Practice

I need a cool web design for my website: www.drkalvoric.com. I would like it to look professional. Keep all the current content and add: Space for video; radio spots (see Silver Cedar Tunes Logo below for those); Quick Inquiry; Friendora link; 5 star rating on Rivo; a map; reviews from former patients. I am open to suggestions.

Target Market(s)

Those seeking individual and marital counseling.

Industry/Entity Type

Mental Health

Number of Pages Required

1 page

Font styles to use
Sans Serif
Other font styles liked:
• I'm open but no hard to read script

Requirements
Must have
• All the content on my home page with link for video and radio spots. List services and degrees and expertices (pics not necessary).
Nice to have
• A video of me and radio conversations (logo of Silver Cedar Tunes radio attached).
Should not have
• Cartoons, comedy, etc.... I don't need pictures of services (marital, depression, etc...) Just list those.

```html
<!DOCTYPE html>
<html lang="en">
<head>
<meta charset="utf-8">
<title>Dr. Marla J. Kalvoric – Psychologist</title>
<link href="https://fonts.googleapis.com/css2?family=Lato:wght@400;700&family=Raleway:wght@600;700;800&display=swap" rel="stylesheet">
<style>
:root{
  --blue:#2b80c4;
  --blue-dark:#1f5f96;
  --gold:#c9a94b;
  --gold-deep:#b3923a;
  --tan:#cdbb80;
  --ink:#2b2b2b;
  --text:#4a4a4a;
  --topbar:#3a3a3a;
  --black:#050505;
  --footer:#262626;
  --footer-base:#1a1a1a;
  --light:#f3f3f3;
}
*{box-sizing:border-box;margin:0;padding:0}
html,body{width:1200px;height:3082px;overflow:hidden}
body{font-family:'Lato',sans-serif;color:var(--text);background:#fff;position:relative}
.heading{font-family:'Raleway',sans-serif;font-weight:700;text-transform:uppercase;color:var(--ink)}
.heading .accent{color:var(--blue)}
.rule{display:block;width:36px;height:3px;background:var(--blue);margin-top:16px}
.btn{display:inline-block;background:var(--blue);color:#fff;font-family:'Raleway',sans-serif;font-weight:700;font-size:14px;text-transform:uppercase;padding:0;text-align:center;border-radius:2px}

/* top bar */
.topbar{height:41px;background:var(--topbar);color:#ddd;font-size:12px;display:flex;align-items:center;padding:0 100px;justify-content:space-between}
.topbar .contact{display:flex;gap:24px;align-items:center}
.topbar .contact span{display:flex;align-items:center;gap:7px}
.topbar .social{display:flex;gap:14px;font-size:11px;color:var(--gold)}

/* header */
.header{height:95px;background:#f7f7f7;display:flex;align-items:center;justify-content:space-between;padding:0 100px;border-bottom:1px solid #e4e4e4}
.brand{font-family:'Lato',sans-serif;font-size:34px;font-weight:400;color:var(--gold)}
.nav{display:flex;align-items:center;gap:0}
.nav a{font-family:'Raleway',sans-serif;font-weight:700;font-size:14px;color:#222;text-transform:uppercase;text-decoration:none;padding:13px 12px}
.nav a.active{background:var(--blue);color:#fff;padding:13px 14px;margin-right:10px}

/* hero */
.hero{position:relative;height:462px;background:linear-gradient(120deg,#d9cfc4 0%,#c9b8a6 35%,#e4dfd8 65%,#bfb4aa 100%)}
.hero .arrow{position:absolute;top:194px;width:28px;height:34px;background:#222;display:flex;align-items:center;justify-content:center}
.hero .arrow.left{left:8px}.hero .arrow.right{right:8px}
.hero .caption{position:absolute;left:0;right:0;bottom:0;height:48px;background:rgba(40,40,40,.55);color:#fff;font-weight:700;font-size:29px;text-align:center;line-height:48px}

/* about */
.about{display:flex;height:485px;background:var(--light)}
.about .portrait{width:600px;height:100%;background:linear-gradient(135deg,#5e7c3a 0%,#9aaa6a 40%,#d9c59a 60%,#4d6fa8 100%)}
.about .body{padding:38px 0 0 37px;width:470px}
.about .heading{font-size:30px}
.about .heading .name{color:var(--gold)}
.about p{font-size:13px;line-height:22px;margin-top:16px;color:#444}
.about h4{font-family:'Raleway',sans-serif;font-weight:700;font-size:15px;color:var(--blue);text-transform:uppercase;margin-top:22px}
.about ul{list-style:none;font-size:12.5px;line-height:23px;margin-top:8px;color:#444}
.about .btn{width:115px;height:40px;line-height:40px;margin-top:18px}

/* expertise */
.expertise{position:relative;height:697px;background:var(--tan)}
.expertise .title{position:absolute;left:0;right:0;top:36px;text-align:center;font-size:30px}
.expertise .title .rule{margin:14px auto 0}
.expertise svg{position:absolute;left:0;top:0}
.skill{position:absolute;width:220px}
.skill h5{font-family:'Raleway',sans-serif;font-weight:700;font-size:16px;color:var(--blue-dark)}
.skill p{font-size:11.5px;line-height:15px;color:#333;margin-top:4px}
.skill.left{text-align:right}

/* media */
.media{height:520px;background:var(--black);position:relative;color:#ddd}
.media .heading{color:#fff;font-size:30px}
.radio{position:absolute;left:100px;top:58px;width:460px}
.radio blockquote{font-size:14px;line-height:24px;margin-top:40px;color:#e5e5e5}
.radio .q{color:var(--gold);font-family:Georgia,serif;font-size:28px;line-height:0;vertical-align:-8px}
.radio cite{display:block;font-style:normal;font-weight:700;color:var(--gold);font-size:15px;margin-top:18px}
.radio .btn{position:absolute;top:330px;left:0;width:108px;height:36px;line-height:36px}
.video-block{position:absolute;left:616px;top:58px;right:0}
.video{position:absolute;left:616px;top:148px;width:584px;height:304px;background:linear-gradient(100deg,#8a7a6a 0%,#c9c1b3 40%,#6f8b79 70%,#b5a993 100%)}
.video .play{position:absolute;left:266px;top:126px}

/* sessions */
.sessions{height:454px;position:relative;background:#fff}
.appointment{position:absolute;left:100px;top:38px;width:325px;height:370px;border:6px solid #e6e6e6;padding:26px 28px}
.appointment h3{font-family:'Raleway',sans-serif;font-weight:700;color:var(--blue);font-size:15px;text-align:center;text-transform:uppercase}
.field{height:33px;border:1px solid #cfcfcf;margin-top:18px;font-size:12px;color:#777;padding:0 12px;display:flex;align-items:center;justify-content:space-between}
.field-row{display:flex;gap:16px}
.field-row .field{flex:1}
.caret{color:var(--gold);font-size:10px}
.appointment .btn{display:block;width:92px;height:36px;line-height:36px;margin:20px auto 0}
.session-list{position:absolute;left:483px;top:60px;width:620px}
.session-list .heading{font-size:30px}
.session-list ul{list-style:none;margin-top:28px}
.session-list li{display:flex;gap:12px;font-size:13.5px;line-height:19px;color:#333;margin-bottom:14px;font-weight:700}
.session-list li svg{flex:none;margin-top:1px}

/* footer */
.footer{height:283px;background:var(--footer);position:relative;color:#ccc;font-size:12px}
.fcol{position:absolute;top:34px}
.fcol h6{font-family:'Raleway',sans-serif;font-weight:700;font-size:17px;color:#fff}
.fcol h6 span{color:var(--blue)}
.quick ul{list-style:none;margin-top:18px;line-height:30px}
.quick li::before{content:"•";color:#aaa;margin-right:8px}
.quick li.active{color:var(--gold)}
.contact-col .row{display:flex;gap:12px;margin-top:20px;line-height:17px}
.contact-col .row b{color:#fff}
.map{position:absolute;left:578px;top:73px;width:281px;height:113px;background:linear-gradient(135deg,#e9e6df,#d6dde0);border:2px solid #fff}
.follow .icons{display:flex;gap:14px;margin-top:22px}
.follow .icon{display:flex;align-items:center;gap:6px;color:#fff;font-size:11px}
.follow .icon i{width:34px;height:34px;border-radius:50%;display:block}
.follow .donate{color:#fff;font-weight:700;font-size:11.5px;line-height:15px;margin-top:36px;width:170px}
.follow .badges{display:flex;gap:12px;margin-top:12px}
.follow .badges i{display:block;width:78px;height:32px;background:#fff}
.copyright{height:45px;background:var(--footer-base);color:#ccc;font-size:12px;text-align:center;line-height:45px}
</style>
</head>
<body>

<div class="topbar">
  <div class="contact">
    <span><svg width="14" height="10" viewBox="0 0 14 10"><rect x=".5" y=".5" width="13" height="9" fill="none" stroke="#c9a94b"/><path d="M1 1l6 5 6-5" fill="none" stroke="#c9a94b"/></svg>mk@drkalvoric.com</span>
    <span><svg width="12" height="12" viewBox="0 0 24 24"><path fill="#c9a94b" d="M6.6 10.8a15 15 0 006.6 6.6l2.2-2.2a1 1 0 011-.2 11.4 11.4 0 003.6.6 1 1 0 011 1V20a1 1 0 01-1 1A17 17 0 013 4a1 1 0 011-1h3.5a1 1 0 011 1 11.4 11.4 0 00.6 3.6 1 1 0 01-.3 1z"/></svg>(949) 555 0142</span>
  </div>
  <div class="social"><span>Friendora</span><span>Chirpline</span></div>
</div>

<header class="header">
  <div class="brand">Dr. Marla J. Kalvoric</div>
  <nav class="nav">
    <a class="active" href="#">Home</a>
    <a href="#">Sessions</a>
    <a href="#">My Expertise</a>
    <a href="#">Resources</a>
    <a href="#">Bio</a>
    <a href="#">Contact Us</a>
  </nav>
</header>

<section class="hero" role="img" aria-label="Photo of a smiling family of four sitting together on a sofa">
  <div class="arrow left"><svg width="8" height="12" viewBox="0 0 8 12"><path d="M7 1L2 6l5 5" stroke="#fff" stroke-width="2" fill="none"/></svg></div>
  <div class="arrow right"><svg width="8" height="12" viewBox="0 0 8 12"><path d="M1 1l5 5-5 5" stroke="#fff" stroke-width="2" fill="none"/></svg></div>
  <div class="caption">I am a phycologist providing individual and marital counseling</div>
</section>

<section class="about">
  <div class="portrait" role="img" aria-label="Portrait photo of the psychologist outdoors in front of greenery"></div>
  <div class="body">
    <h2 class="heading">About <span class="name">Dr. Marla J. Kalvoric</span></h2>
    <span class="rule"></span>
    <p>While I acknowledge the importance of my education, I also appreciate the role my experiences have played in allowing me to relate so well to others. Allow me to share those I feel are most relevant with you.</p>
    <p style="margin-top:10px">I survived an abusive childhood that my mother and sister unfortunately did not.&nbsp; And it was my grief and desire to become stronger than my past that led me to counseling. A process that clearly changed my life</p>
    <h4>My Degrees</h4>
    <ul>
      <li>Doctoral Degree in Clinical Psychology</li>
      <li>Masters Degree in Counseling Psychology</li>
      <li>Doctoral Internship, Bayline Medical Center</li>
      <li>Masters Internship, Westbrook Clinic</li>
    </ul>
    <a class="btn" href="#">Read More</a>
  </div>
</section>

<section class="expertise">
  <svg width="1200" height="697" viewBox="0 0 1200 697">
    <g stroke="#7d8aa0" stroke-width="1.5" fill="none">
      <line x1="569" y1="380" x2="569" y2="196"/>
      <line x1="569" y1="380" x2="707" y2="277"/>
      <line x1="569" y1="380" x2="707" y2="484"/>
      <line x1="569" y1="380" x2="569" y2="607"/>
      <line x1="569" y1="380" x2="431" y2="484"/>
      <line x1="569" y1="380" x2="431" y2="277"/>
      <polyline points="420,144 470,144 520,180"/>
      <polyline points="270,271 376,271"/>
      <polyline points="280,493 376,493"/>
      <polyline points="868,267 762,277"/>
      <polyline points="873,454 762,484"/>
      <polyline points="735,612 650,612 615,640"/>
    </g>
    <g fill="#2b80c4">
      <circle cx="420" cy="144" r="3"/><circle cx="270" cy="271" r="3"/><circle cx="280" cy="493" r="3"/>
      <circle cx="868" cy="267" r="3"/><circle cx="873" cy="454" r="3"/><circle cx="735" cy="612" r="3"/>
    </g>
    <g>
      <g fill="#f6f0dc"><circle cx="569" cy="196" r="56"/><circle cx="707" cy="277" r="56"/><circle cx="707" cy="484" r="56"/><circle cx="569" cy="607" r="56"/><circle cx="431" cy="484" r="56"/><circle cx="431" cy="277" r="56"/></g>
      <g fill="#b3923a"><circle cx="569" cy="196" r="49"/><circle cx="707" cy="277" r="49"/><circle cx="707" cy="484" r="49"/><circle cx="569" cy="607" r="49"/><circle cx="431" cy="484" r="49"/><circle cx="431" cy="277" r="49"/></g>
      <circle cx="569" cy="380" r="72" fill="#f6f0dc"/>
      <circle cx="569" cy="380" r="64" fill="#1f6aa8"/>
      <text x="569" y="375" text-anchor="middle" font-family="Lato, sans-serif" font-size="17" fill="#e6cf85">Dr. Marla J.</text>
      <text x="569" y="397" text-anchor="middle" font-family="Lato, sans-serif" font-size="17" fill="#e6cf85">Kalvoric</text>
    </g>
  </svg>
  <h2 class="heading title">My <span class="accent">Expertise</span><span class="rule"></span></h2>
  <div class="skill left" style="left:190px;top:134px"><h5>Dating</h5><p>Lorem ipsum dolor sit amensectetuer adipiscing elit, seddiam no</p></div>
  <div class="skill left" style="left:42px;top:261px"><h5>Life Management</h5><p>Lorem ipsum dolor sit amensectetuer adipiscing elit,</p></div>
  <div class="skill left" style="left:52px;top:483px"><h5>Personality Disorders</h5><p>Lorem ipsum dolor sit amensectetuer adipiscing elit,</p></div>
  <div class="skill" style="left:876px;top:257px"><h5>Marriage</h5><p>Lorem ipsum dolor sit amensectetuer adipiscing elit, seddiam no</p></div>
  <div class="skill" style="left:881px;top:444px"><h5>Parenting &amp; Professional Relationships</h5><p>Lorem ipsum dolor sit amensectetuer adipiscing elit, seddiam no</p></div>
  <div class="skill" style="left:743px;top:602px;width:260px"><h5>Depression &amp; Anxiety Issues</h5><p>Lorem ipsum dolor sit amensectetuer<br>adipiscing elit, seddiam no</p></div>
</section>

<section class="media">
  <div class="radio">
    <h2 class="heading">Radio <span class="accent">Conversations</span></h2>
    <span class="rule"></span>
    <blockquote><span class="q">“</span> Lorem ipsum dolor sit amet, consectetuer adipiscing elit, sed diam nonummy tincidunt ut laoreet dolore magna quam erat volutpat. Ut wisi enim ad minim veniam, quis nostrud exerci tation ullamcorper suscipit lobortis nisl ut aliquip ex ea commodo consequat. Duis autem vel eum iriure.laoreet dolore magna quam erat <span class="q">”</span></blockquote>
    <cite>Owen Maddox</cite>
    <a class="btn" href="#">View All</a>
  </div>
  <div class="video-block">
    <h2 class="heading">View <span class="accent">Video</span></h2>
    <span class="rule"></span>
  </div>
  <div class="video" role="img" aria-label="Video still of a counseling session with a man, a woman and a child">
    <svg class="play" width="50" height="50" viewBox="0 0 50 50"><circle cx="25" cy="25" r="23" fill="rgba(0,0,0,.25)" stroke="#fff" stroke-width="3"/><path d="M20 15l14 10-14 10z" fill="#fff"/></svg>
  </div>
</section>

<section class="sessions">
  <form class="appointment">
    <h3>Schedule an Appointment</h3>
    <div class="field" style="margin-top:22px">Full Name</div>
    <div class="field">Phone Number</div>
    <div class="field-row">
      <div class="field">Date<span class="caret">▼</span></div>
      <div class="field">Time<span class="caret">▼</span></div>
    </div>
    <div class="field">Location<span class="caret">▼</span></div>
    <span class="btn">Submit</span>
  </form>
  <div class="session-list">
    <h2 class="heading">My <span class="accent">Sessions</span></h2>
    <span class="rule"></span>
    <ul>
      <li><svg width="16" height="16" viewBox="0 0 16 16"><path d="M2 8l4 5 8-11" stroke="#2b80c4" stroke-width="2.5" fill="none"/></svg>Individual sessions are 50 minutes in length</li>
      <li><svg width="16" height="16" viewBox="0 0 16 16"><path d="M2 8l4 5 8-11" stroke="#2b80c4" stroke-width="2.5" fill="none"/></svg>Marriage sessions are typically 50 to 75 minutes in length</li>
      <li><svg width="16" height="16" viewBox="0 0 16 16"><path d="M2 8l4 5 8-11" stroke="#2b80c4" stroke-width="2.5" fill="none"/></svg>Family sessions are 60 to 75 minutes in length</li>
      <li><svg width="16" height="16" viewBox="0 0 16 16"><path d="M2 8l4 5 8-11" stroke="#2b80c4" stroke-width="2.5" fill="none"/></svg>Divorce Mediation sessions are primarily conducted with individual sessions for each spouse with meetings as a couple kept to a minimum</li>
      <li><svg width="16" height="16" viewBox="0 0 16 16"><path d="M2 8l4 5 8-11" stroke="#2b80c4" stroke-width="2.5" fill="none"/></svg>Custody Evaluation sessions are usually initiated by each parties attorneys or the presiding judge</li>
      <li><svg width="16" height="16" viewBox="0 0 16 16"><path d="M2 8l4 5 8-11" stroke="#2b80c4" stroke-width="2.5" fill="none"/></svg>Testing sessions vary in length dependent upon the nature of the psychological assessment needed</li>
    </ul>
  </div>
</section>

<footer class="footer">
  <div class="fcol quick" style="left:100px">
    <h6>Quick <span>Links</span></h6>
    <ul>
      <li class="active">Home</li><li>Sessions</li><li>My Expertise</li><li>Resources</li><li>Bio</li><li>Contact Us</li>
    </ul>
  </div>
  <div class="fcol contact-col" style="left:288px">
    <h6>Contact <span>Details</span></h6>
    <div class="row"><svg width="12" height="16" viewBox="0 0 12 16"><path d="M6 0a6 6 0 016 6c0 4-6 10-6 10S0 10 0 6a6 6 0 016-6z" fill="#ccc"/><circle cx="6" cy="6" r="2.2" fill="#262626"/></svg><div><b>Dr. Marla J. Kalvoric</b><br>740 Harbor Lane #118<br>Seaview, CA 92601</div></div>
    <div class="row"><svg width="13" height="13" viewBox="0 0 24 24"><path fill="#ccc" d="M6.6 10.8a15 15 0 006.6 6.6l2.2-2.2a1 1 0 011-.2 11.4 11.4 0 003.6.6 1 1 0 011 1V20a1 1 0 01-1 1A17 17 0 013 4a1 1 0 011-1h3.5a1 1 0 011 1 11.4 11.4 0 00.6 3.6 1 1 0 01-.3 1z"/></svg>(949) 555 0142</div>
    <div class="row"><svg width="11" height="15" viewBox="0 0 11 15"><rect x=".5" y=".5" width="10" height="14" rx="1.5" fill="none" stroke="#ccc"/><circle cx="5.5" cy="12" r="1" fill="#ccc"/></svg>(949) 555 0142</div>
    <div class="row"><svg width="14" height="10" viewBox="0 0 14 10"><rect x=".5" y=".5" width="13" height="9" fill="none" stroke="#ccc"/><path d="M1 1l6 5 6-5" fill="none" stroke="#ccc"/></svg>mk@drkalvoric.com</div>
  </div>
  <div class="fcol" style="left:578px"><h6>Location <span>Map</span></h6></div>
  <div class="map" role="img" aria-label="Street map showing the office location"></div>
  <div class="fcol follow" style="left:940px">
    <h6>Follow <span>Us</span></h6>
    <div class="icons">
      <span class="icon"><i style="background:#3b5998"></i>Friendora</span>
      <span class="icon"><i style="background:#2aa3e0"></i>Chirpline</span>
    </div>
    <p class="donate">A portion of all revenue is donated to</p>
    <div class="badges"><i></i><i></i></div>
  </div>
</footer>
<div class="copyright">Copyright © 2016 Dr. Marla J. Kalvoric. All Rights Reserved</div>

</body>
</html>
```